UI Redesign For Mobile Events iPhone App

We need a new UI design for our Social Events mobile app. Our app called Vessa is geared to help users find trending events in their local area. We show visual metrics on percent full and male female ratio and age group ratings. We want people to see whats going on at event before they get there through our app. Also we have a group chat portion to our app that we need included in the design. We would like to see a fresh, clean, and easy to use user interface that uses colors like, purple, blue and or hot pink.You may visit our website myvessa.example for more information about what our app is geared to do.
Updates

Target Market(s)

Our target market people that use social networks and attend social events ranging from ages 16-44.

Industry/Entity Type

Events

Requirements
Must have
• We would like to see an Example layout of all screens. (UPDATE: Please use our current background in your design, A PSD has been uploaded for you to grab the background. The Vessa Logo is NOT required to be included at the top of every screen)

-Profile Screen: Shows points earned, events attending, events created
-Event Listings Screen: Must have large image for event, visual metrics, date& time, location, attend button, invite friends button, Label for user who created the event
-Event Description Page: Shows everything as the event listing, has a description of the event, shows friends that are attending, points available
-Group Messaging Screen
-Slide Out Navigation Screen
-Notification Screen
-Ticket Screen
-Friends Activity Screen
-Friends Profile View: Shows events they've attended and points they've earned under their contact picture; invite button
-Sign-In Screen
-Register Screen

A way to label/categorize our different types of events:
-Nightlife
-Family
-Live Music & Concerts
-Restaurants
Group Chat Layout
Visual Meters for Percent Full, Male Female Ratio, Age Rating

```html
<!DOCTYPE html>
<html lang="en">
<head>
<meta charset="utf-8">
<title>My Vessa Screen</title>
<link href="https://fonts.googleapis.com/css2?family=Roboto:wght@300;400&display=swap" rel="stylesheet">
<style>
  :root {
    --stage-bg: #f1e7e9;
    --stage-glow: #faf6f6;
    --ink: #111111;
    --screen-purple: #7b3aa4;
    --bar-purple: #4b1768;
    --panel-lilac: #f3e6fb;
    --panel-line: #e2d2ee;
    --label-grey: #8a7f90;
    --accent-purple: #4b1a8c;
    --avatar: #262626;
    --white: #ffffff;
  }
  * { box-sizing: border-box; margin: 0; padding: 0; }
  html, body { width: 1200px; height: 1000px; overflow: hidden; }
  body {
    position: relative;
    font-family: "Roboto", Arial, sans-serif;
    background: radial-gradient(ellipse at 60% 45%, var(--stage-glow) 0%, var(--stage-bg) 75%);
  }

  .headline {
    position: absolute; left: 600px; top: 92px; width: 590px;
    text-align: center; color: var(--ink);
  }
  .headline-title { font-size: 63px; font-weight: 400; line-height: 1; letter-spacing: 0.5px; }
  .headline-sub { font-size: 38px; font-weight: 300; line-height: 1; margin-top: 12px; }

  .app-screen {
    position: absolute; left: 18px; top: 15px; width: 338px; height: 604px;
    background: var(--screen-purple); border: 1px solid #3c1458; color: var(--white);
    overflow: hidden;
  }
  .status-bar {
    position: absolute; left: 0; top: 0; width: 100%; height: 22px;
    font-size: 12px; display: flex; align-items: center; padding: 0 6px;
  }
  .status-left { display: flex; align-items: center; gap: 4px; }
  .status-time { position: absolute; left: 0; right: 0; text-align: center; font-size: 12.5px; }
  .status-right { margin-left: auto; display: flex; align-items: center; gap: 4px; }

  .nav-back { position: absolute; left: 22px; top: 50px; width: 12px; height: 18px; }
  .screen-title { position: absolute; left: 0; right: 0; top: 47px; text-align: center; font-size: 33px; font-weight: 400; }

  .bar {
    position: absolute; left: 10px; width: 319px; height: 47px; background: var(--bar-purple);
    display: flex; align-items: center; justify-content: center; font-size: 18px;
  }
  .bar-icon { position: absolute; right: 13px; top: 12px; width: 22px; height: 22px; }
  .group-select { top: 93px; }
  .view-all { top: 333px; }
  .create-group { top: 404px; }

  .recent-panel {
    position: absolute; left: 10px; top: 163px; width: 319px; height: 170px; background: var(--panel-lilac);
  }
  .recent-head {
    height: 47px; border-bottom: 1px solid var(--panel-line);
    display: flex; align-items: center; padding: 0 14px; font-size: 14.5px; color: var(--label-grey);
  }
  .recent-add { margin-left: auto; display: flex; align-items: center; gap: 6px; color: var(--accent-purple); font-size: 15px; }
  .member { position: absolute; top: 60px; width: 80px; text-align: center; color: var(--ink); font-size: 14px; }
  .member-avatar { width: 77px; height: 77px; margin: 0 auto 10px; border-radius: 50%; background: var(--avatar); border: 1px solid #111; }

  .tab-bar { position: absolute; left: 0; top: 507px; width: 100%; height: 90px; }
  .tab { position: absolute; top: 0; width: 70px; text-align: center; font-size: 12.5px; }
  .tab-icon {
    width: 55px; height: 55px; margin: 0 auto 9px; border-radius: 50%;
    border: 1.5px solid var(--white); display: flex; align-items: center; justify-content: center;
  }
  .tab-active .tab-icon { background: var(--white); }
</style>
</head>
<body>

<div class="headline">
  <div class="headline-title">My Vessa Screen</div>
  <div class="headline-sub">Flat Style</div>
</div>

<main class="app-screen">
  <div class="status-bar">
    <div class="status-left">
      <svg width="36" height="8" viewBox="0 0 36 8" aria-hidden="true">
        <circle cx="3.5" cy="4" r="3" fill="#fff"/><circle cx="10.5" cy="4" r="3" fill="#fff"/><circle cx="17.5" cy="4" r="3" fill="#fff"/>
        <circle cx="24.5" cy="4" r="2.6" fill="none" stroke="#fff"/><circle cx="31.5" cy="4" r="2.6" fill="none" stroke="#fff"/>
      </svg>
      <span>NOVA</span>
      <svg width="14" height="10" viewBox="0 0 14 10" aria-hidden="true">
        <path d="M1 3.5a9 9 0 0 1 12 0M3 5.8a6 6 0 0 1 8 0M5 8a3 3 0 0 1 4 0" fill="none" stroke="#fff" stroke-width="1.3"/>
      </svg>
    </div>
    <div class="status-time">4:21 PM</div>
    <div class="status-right">
      <svg width="7" height="11" viewBox="0 0 7 11" aria-hidden="true"><path d="M1 3l5 5-2.5 2V1L6 3 1 8" fill="none" stroke="#fff" stroke-width="1"/></svg>
      <span>100%</span>
      <svg width="26" height="11" viewBox="0 0 26 11" aria-hidden="true">
        <rect x="0.5" y="0.5" width="22" height="10" rx="2" fill="none" stroke="#fff"/>
        <rect x="2" y="2" width="19" height="7" rx="1" fill="#fff"/><rect x="23.5" y="3.5" width="2" height="4" fill="#fff"/>
      </svg>
    </div>
  </div>

  <svg class="nav-back" viewBox="0 0 12 18" aria-label="Back"><path d="M9 3L3 9l6 6" fill="none" stroke="#fff" stroke-width="2"/></svg>
  <h1 class="screen-title">My Vessa</h1>

  <div class="bar group-select">Sloths
    <svg class="bar-icon" viewBox="0 0 22 22" aria-hidden="true"><circle cx="11" cy="11" r="11" fill="#fff"/><path d="M6.5 9l4.5 4.5L15.5 9" fill="none" stroke="#4b1768" stroke-width="2.4"/></svg>
  </div>

  <section class="recent-panel">
    <div class="recent-head">RECENTLY ADDED
      <span class="recent-add">
        <svg width="22" height="22" viewBox="0 0 22 22" aria-hidden="true"><circle cx="11" cy="11" r="11" fill="#4b1a8c"/><path d="M11 6v10M6 11h10" stroke="#fff" stroke-width="2"/></svg>
        Add
      </span>
    </div>
    <div class="member" style="left:28px"><div class="member-avatar"></div>user1</div>
    <div class="member" style="left:130px"><div class="member-avatar"></div>user1</div>
    <div class="member" style="left:232px"><div class="member-avatar"></div>user3</div>
  </section>

  <div class="bar view-all">View All
    <svg class="bar-icon" viewBox="0 0 22 22" aria-hidden="true"><circle cx="11" cy="11" r="11" fill="#fff"/><path d="M9 6.5l4.5 4.5L9 15.5" fill="none" stroke="#4b1768" stroke-width="2.4"/></svg>
  </div>

  <div class="bar create-group">Create a Vessa</div>

  <nav class="tab-bar">
    <div class="tab" style="left:16px">
      <div class="tab-icon">
        <svg width="34" height="30" viewBox="0 0 34 30" aria-hidden="true" fill="none" stroke="#fff" stroke-width="1.5">
          <circle cx="13" cy="8" r="5"/><path d="M3 27c0-7 4-11 10-11s10 4 10 11z"/>
          <circle cx="23" cy="12" r="4"/><path d="M19 27c0-5 2-9 5.5-9S31 22 31 27z"/>
        </svg>
      </div>Profile
    </div>
    <div class="tab tab-active" style="left:118px">
      <div class="tab-icon"></div>My Vessa
    </div>
    <div class="tab" style="left:193px">
      <div class="tab-icon">
        <svg width="30" height="30" viewBox="0 0 30 30" aria-hidden="true" fill="none" stroke="#fff" stroke-width="1.5">
          <path d="M4 15L15 4h10v10L14 25z"/><circle cx="21" cy="8.5" r="1.8"/>
        </svg>
      </div>Tickets
    </div>
    <div class="tab" style="left:251px">
      <div class="tab-icon">
        <svg width="32" height="32" viewBox="0 0 32 32" aria-hidden="true" fill="#fff">
          <circle cx="16" cy="16" r="4" fill="none" stroke="#fff" stroke-width="1.5"/>
          <circle cx="16" cy="5" r="2"/><circle cx="16" cy="27" r="2"/><circle cx="5" cy="16" r="2"/><circle cx="27" cy="16" r="2"/>
          <circle cx="8.2" cy="8.2" r="2"/><circle cx="23.8" cy="8.2" r="2"/><circle cx="8.2" cy="23.8" r="2"/><circle cx="23.8" cy="23.8" r="2"/>
        </svg>
      </div>Events
    </div>
  </nav>
</main>

</body>
</html>
```